Online training business needs new website

We need a new wordpress website as a result of a rebranding. The business is a crisis management training company focussed on online training and simulation exercises. We only need a 4 page site - home, about us, contact us and blog. However we must be able to add additional tabs in the header to redirect to our sales and marketing system (Kartra). As these change from time to time, we must be able to add and delete as required.The site must be editable by us, with a basic understanding of wordpress and no understanding of coding. We don't want to have to employ someone to change text, add posts or add a new workshops etc. The theme chosen must be easy to edit by a beginner.

Target Market(s)

Senior managers food and consumer goods companies

Industry/Entity Type

Consulting

Coding

Coded - Design and coding required

Font styles to use
Sans Serif

Requirements
Must have
• Home page, about us, contact us, blog
• Colour scheme from logo (attached) - maroon, blue and grey
• If you go to the current website "tidewellcollege.com" and click on the "workshops" tab you will see the content I need on the home page for the plumvantage.com site
Nice to have
• Modern, simple and minimalist design is preferred

```html
<!DOCTYPE html>
<html lang="en">
<head>
<meta charset="utf-8">
<title>About Us – Plum Vantage</title>
<link rel="stylesheet" href="https://fonts.googleapis.com/css2?family=Roboto:wght@400;500;700&family=Open+Sans:wght@400&display=swap">
<style>
  :root {
    --maroon: #7d0f3e;
    --navy: #0c3c78;
    --text: #4a4a4a;
    --grey: #555;
    --rule: #a9b8cc;
    --white: #ffffff;
  }
  * { box-sizing: border-box; margin: 0; padding: 0; }
  html, body { width: 1198px; height: 1200px; overflow: hidden; background: var(--white); }
  body { position: relative; font-family: "Roboto", Arial, sans-serif; }

  .site-header { position: absolute; top: 0; left: 0; width: 1198px; height: 112px; background: var(--white); z-index: 3; }
  .brand-badge {
    position: absolute; left: 150px; top: -20px; width: 156px; height: 158px;
    border-radius: 50%; background: var(--white);
    display: flex; align-items: center; justify-content: center;
  }
  .brand-name {
    font-family: "Roboto", Arial, sans-serif; font-weight: 700; font-size: 25px;
    color: var(--maroon); line-height: 1.05; text-align: center; margin-top: 18px;
  }
  .main-nav { position: absolute; top: 50px; left: 372px; display: flex; gap: 21px; }
  .main-nav a, .footer-nav a {
    font-size: 16.5px; color: var(--navy); text-decoration: none; letter-spacing: 0.1px;
  }
  .main-nav a.is-current { color: var(--maroon); }

  .hero { position: absolute; top: 112px; left: 0; width: 1198px; height: 430px; }
  .hero-photo {
    position: absolute; inset: 0;
    background: radial-gradient(ellipse at 45% 70%, #6b5437 0%, #3b2e22 40%, #1f1a16 100%);
  }
  .hero-title {
    position: absolute; top: 152px; left: 0; width: 1198px; text-align: center;
    font-size: 51px; font-weight: 700; color: var(--white); letter-spacing: 0.5px;
  }
  .hero-curve { position: absolute; left: 0; top: 0; }

  .about { position: absolute; top: 560px; left: 0; width: 1198px; }
  .about-portrait { position: absolute; left: 146px; top: 5px; }
  .about-copy { position: absolute; left: 484px; top: 15px; width: 570px; }
  .about-title { font-size: 37px; font-weight: 400; color: var(--navy); line-height: 1.1; margin-bottom: 16px; }
  .about-title .accent { color: var(--maroon); }
  .about-copy p {
    font-family: "Open Sans", Arial, sans-serif; font-size: 15.2px;
    line-height: 31px; color: var(--text); margin-bottom: 30px;
  }

  .site-footer { position: absolute; top: 1053px; left: 0; width: 1198px; border-top: 1px solid var(--rule); }
  .footer-nav { display: flex; justify-content: center; gap: 21px; margin-top: 49px; }
  .copyright { text-align: center; margin-top: 15px; font-size: 16.5px; color: var(--grey); }
</style>
</head>
<body>
  <header class="site-header">
    <div class="brand-badge"><span class="brand-name">PLUM<br>VANTAGE</span></div>
    <nav class="main-nav">
      <a class="is-current" href="#">ABOUT US</a>
      <a href="#">WORKSHOPS</a>
      <a href="#">ONLINE COURSE</a>
      <a href="#">SIMULATIONS</a>
      <a href="#">CONTACT US</a>
      <a href="#">BLOG</a>
    </nav>
  </header>

  <section class="hero">
    <div class="hero-photo" role="img" aria-label="Hand stopping a row of falling wooden dominoes on a dark table"></div>
    <h1 class="hero-title">ABOUT US</h1>
    <svg class="hero-curve" width="1198" height="430" viewBox="0 0 1198 430">
      <path d="M0 424 Q599 312 1198 424 L1198 430 L0 430 Z" fill="#ffffff"/>
      <path d="M104 411 Q599 330 1094 411 Q599 338 104 411 Z" fill="#0c3c78"/>
      <circle cx="598" cy="362" r="38" fill="#ffffff"/>
    </svg>
  </section>

  <section class="about">
    <svg class="about-portrait" width="320" height="320" viewBox="0 0 320 320" role="img" aria-label="Businesswoman speaking in a meeting">
      <defs>
        <linearGradient id="portraitTone" x1="0" y1="0" x2="1" y2="1">
          <stop offset="0" stop-color="#c9cfd6"/>
          <stop offset="0.5" stop-color="#d9dfe8"/>
          <stop offset="1" stop-color="#b48a5e"/>
        </linearGradient>
      </defs>
      <circle cx="158" cy="160" r="158" fill="#0c3c78"/>
      <circle cx="172" cy="162" r="146" fill="url(#portraitTone)"/>
    </svg>
    <div class="about-copy">
      <h2 class="about-title"><span class="accent">ABOUT</span> PLUM VANTAGE</h2>
      <p>Donec convallis pede venenatis nibh Duis quam Nam eget lacus Aliquam erat volutpat Quisque dignissim congue leoMauris vel lacus vitae felis vestibulum volutpat Etiam est nunc venenatis in tristique eu imperdiet ac nisl Cum sociis natoque penatibus et magnis dis parturient montes nascetur ridiculus mus In iaculis facilisis massa Etiam eu urna Sed porta</p>
      <p>Suspendisse quam leo molestie sed luctus quis feugiat in pede Fusce tellus Sed metus augue convallis et vehicula ut pulvinar eu ante Integer orci tellus tristique vitae consequat nec porta vel lectus Nulla sit amet diam Duis non nunc Nulla rhoncus dictum metus Curabitur tristique mi condim</p>
    </div>
  </section>

  <footer class="site-footer">
    <nav class="footer-nav">
      <a href="#">ABOUT US</a>
      <a href="#">WORKSHOPS</a>
      <a href="#">ONLINE COURSE</a>
      <a href="#">SIMULATIONS</a>
      <a href="#">CONTACT US</a>
      <a href="#">BLOG</a>
    </nav>
    <p class="copyright">© 2019 Company Name&nbsp; All right reserved</p>
  </footer>
</body>
</html>
```